Design logo and business card.

Design and construct logo and card for my business which is an over seeing company of other smaller businesses. The companies name is ember4 business works. Im open to any ideas but i am looking for a very cool contemporary design with a very prestige feel. The card can be either single or double sided, Thank you and i will look forward to your submissions.

Business

• Company name, email, website, telephone, my name. Cool modern look with a prestige feel.

```html
<!DOCTYPE html>
<html lang="en">
<head>
<meta charset="utf-8">
<title>ember4 business works – card options</title>
<link href="https://fonts.googleapis.com/css2?family=Open+Sans:wght@400;600&family=Archivo:wght@800&display=swap" rel="stylesheet">
<style>
  :root {
    --page: #ffffff;
    --card-top: #2b2b2b;
    --card-top-deep: #1f1f1f;
    --card-bottom: #232323;
    --ink-white: #ffffff;
    --lime: #8dc63f;
    --silver: #d2d2d2;
    --label: #1b1b1b;
  }
  * { box-sizing: border-box; margin: 0; padding: 0; }
  html, body { width: 1200px; height: 1000px; overflow: hidden; background: var(--page); }
  body { position: relative; font-family: "Open Sans", Arial, sans-serif; }

  .option-number {
    position: absolute;
    font-family: "Archivo", Arial, sans-serif;
    font-weight: 800;
    font-size: 60px;
    line-height: 1;
    color: var(--label);
  }

  .card {
    position: absolute;
    width: 380px;
    height: 219px;
    border-radius: 18px;
    overflow: hidden;
    background: var(--card-bottom);
    color: var(--ink-white);
  }
  .card-texture {
    position: absolute;
    left: 0; top: 0; width: 100%;
    background: radial-gradient(ellipse at 50% 40%, var(--card-top) 0%, var(--card-top-deep) 100%);
  }
  .card-front .card-texture { height: 100%; }
  .card-back .card-texture { height: 117px; }

  .brand-name {
    position: absolute;
    left: 0; width: 100%;
    top: 82px;
    text-align: center;
    font-size: 26px;
    font-weight: 400;
    letter-spacing: 0.5px;
  }
  .accent-lime .brand-name { color: var(--lime); }
  .accent-silver .brand-name { color: var(--silver); }

  .web-rule {
    position: absolute;
    left: 0; top: 186px;
    width: 100%; height: 12px;
  }
  .web-address {
    position: absolute;
    top: 185px;
    left: 232px;
    font-size: 11px;
    color: var(--ink-white);
  }

  .company-title {
    position: absolute;
    left: 0; width: 100%;
    top: 76px;
    text-align: center;
    font-size: 18.5px;
    letter-spacing: 0.2px;
  }
  .divider {
    position: absolute;
    left: 0; top: 115px;
    width: 100%; height: 5px;
  }
  .accent-lime .divider { background: var(--lime); }
  .accent-silver.tone-dark .divider { background: linear-gradient(90deg, #eeeeee 0%, #9a9a9a 45%, #3a3a3a 100%); }
  .accent-silver.tone-light .divider { background: linear-gradient(90deg, #f2f2f2 0%, #bcbcbc 55%, #7a7a7a 100%); }

  .holder-name {
    position: absolute;
    left: 0; width: 100%;
    top: 138px;
    text-align: center;
    font-size: 15px;
  }
  .accent-lime .holder-name { color: var(--lime); }
  .contact-line {
    position: absolute;
    left: 0; width: 100%;
    text-align: center;
    font-size: 10.5px;
    font-weight: 600;
  }
  .contact-phone { top: 163px; }
  .contact-email { top: 181px; }
  .contact-line svg { width: 8px; height: 8px; margin-right: 3px; vertical-align: -1px; }
</style>
</head>
<body>

<div class="option-number" style="left:88px;top:88px;">1</div>
<div class="option-number" style="left:1075px;top:80px;">2</div>
<div class="option-number" style="left:58px;top:733px;">3</div>
<div class="option-number" style="left:1077px;top:713px;">4</div>

<svg width="0" height="0" style="position:absolute">
  <defs>
    <linearGradient id="silver-dark" x1="0" x2="1"><stop offset="0" stop-color="#f0f0f0"/><stop offset="0.5" stop-color="#8a8a8a"/><stop offset="1" stop-color="#3a3a3a"/></linearGradient>
    <linearGradient id="silver-light" x1="0" x2="1"><stop offset="0" stop-color="#f4f4f4"/><stop offset="0.6" stop-color="#b5b5b5"/><stop offset="1" stop-color="#8a8a8a"/></linearGradient>
    <linearGradient id="silver-tab" x1="0" x2="1"><stop offset="0" stop-color="#555"/><stop offset="1" stop-color="#f2f2f2"/></linearGradient>
    <symbol id="icon-phone" viewBox="0 0 8 8"><rect x="2" y="0.5" width="4" height="7" rx="0.8" fill="none" stroke="#fff" stroke-width="0.9"/></symbol>
    <symbol id="icon-mail" viewBox="0 0 8 8"><rect x="0.5" y="1.5" width="7" height="5" fill="none" stroke="#fff" stroke-width="0.8"/><path d="M0.5 1.5 L4 4.5 L7.5 1.5" fill="none" stroke="#fff" stroke-width="0.8"/></symbol>
  </defs>
</svg>

<!-- Option 1 -->
<div class="card card-front accent-lime" style="left:210px;top:2px;">
  <div class="card-texture" role="img" aria-label="Dark damask ornament pattern"></div>
  <div class="brand-name">ember4 business works</div>
  <svg class="web-rule" viewBox="0 0 380 12" preserveAspectRatio="none">
    <rect x="0" y="3" width="222" height="7" fill="var(--lime)"/>
    <polygon points="346,3 380,3 380,10 342,10" fill="var(--lime)"/>
  </svg>
  <div class="web-address">www. ember-4.com</div>
</div>
<div class="card card-back accent-lime" style="left:207px;top:259px;">
  <div class="card-texture" role="img" aria-label="Dark damask ornament pattern"></div>
  <div class="company-title">EMBER4 BUSINESS WORKS</div>
  <div class="divider"></div>
  <div class="holder-name">LENA MORROW</div>
  <div class="contact-line contact-phone"><svg><use href="#icon-phone"/></svg>+34 600 555 019</div>
  <div class="contact-line contact-email"><svg><use href="#icon-mail"/></svg>info@ember-4.com</div>
</div>

<!-- Option 2 -->
<div class="card card-front accent-lime" style="left:624px;top:2px;">
  <div class="card-texture" role="img" aria-label="Dark damask ornament pattern"></div>
  <div class="brand-name">ember4 business works</div>
  <svg class="web-rule" viewBox="0 0 380 12" preserveAspectRatio="none">
    <rect x="0" y="3" width="222" height="7" fill="var(--lime)"/>
    <polygon points="346,3 380,3 380,10 342,10" fill="var(--lime)"/>
  </svg>
  <div class="web-address">www. ember-4.com</div>
</div>
<div class="card card-back accent-lime" style="left:621px;top:259px;">
  <div class="card-texture" role="img" aria-label="Dark damask ornament pattern"></div>
  <div class="company-title">EMBER4 BUSINESS WORKS</div>
  <div class="divider"></div>
  <div class="holder-name">LENA MORROW</div>
  <div class="contact-line contact-phone"><svg><use href="#icon-phone"/></svg>+34 600 555 019</div>
  <div class="contact-line contact-email"><svg><use href="#icon-mail"/></svg>info@ember-4.com</div>
</div>

<!-- Option 3 -->
<div class="card card-front accent-silver tone-dark" style="left:202px;top:520px;">
  <div class="card-texture" role="img" aria-label="Dark damask ornament pattern"></div>
  <div class="brand-name">ember4 business works</div>
  <svg class="web-rule" viewBox="0 0 380 12" preserveAspectRatio="none">
    <rect x="0" y="3" width="222" height="7" fill="url(#silver-dark)"/>
    <polygon points="350,3 380,3 380,10 346,10" fill="url(#silver-tab)"/>
  </svg>
  <div class="web-address">www. ember-4.com</div>
</div>
<div class="card card-back accent-silver tone-dark" style="left:200px;top:777px;">
  <div class="card-texture" role="img" aria-label="Dark damask ornament pattern"></div>
  <div class="company-title">EMBER4 BUSINESS WORKS</div>
  <div class="divider"></div>
  <div class="holder-name">LENA MORROW</div>
  <div class="contact-line contact-phone"><svg><use href="#icon-phone"/></svg>+34 600 555 019</div>
  <div class="contact-line contact-email"><svg><use href="#icon-mail"/></svg>info@ember-4.com</div>
</div>

<!-- Option 4 -->
<div class="card card-front accent-silver tone-light" style="left:606px;top:520px;">
  <div class="card-texture" role="img" aria-label="Dark damask ornament pattern"></div>
  <div class="brand-name">ember4 business works</div>
  <svg class="web-rule" viewBox="0 0 380 12" preserveAspectRatio="none">
    <rect x="0" y="3" width="222" height="7" fill="url(#silver-light)"/>
    <polygon points="350,3 380,3 380,10 346,10" fill="url(#silver-tab)"/>
  </svg>
  <div class="web-address">www. ember-4.com</div>
</div>
<div class="card card-back accent-silver tone-light" style="left:614px;top:777px;">
  <div class="card-texture" role="img" aria-label="Dark damask ornament pattern"></div>
  <div class="company-title">EMBER4 BUSINESS WORKS</div>
  <div class="divider"></div>
  <div class="holder-name">LENA MORROW</div>
  <div class="contact-line contact-phone"><svg><use href="#icon-phone"/></svg>+34 600 555 019</div>
  <div class="contact-line contact-email"><svg><use href="#icon-mail"/></svg>info@ember-4.com</div>
</div>

</body>
</html>
```